Quran Jar

So I need help designing bespoke jars which will contain religious quotes.

So there will be three jars in total sold either individually or in two or as a three.

Each Jar will have different contents and preferably a different colour scheme.

I want the packaging to be customised with my branding and logo and to make the product stand out I am thinking of packing it further in a cotton bag with my branding.

```html
<!DOCTYPE html>
<html lang="en">
<head>
<meta charset="utf-8">
<title>Quran Jar – Packaging Labels</title>
<link rel="stylesheet" href="https://fonts.googleapis.com/css2?family=Quicksand:wght@500&display=swap">
<style>
  :root {
    --page: #ffffff;
    --box-black: #0c0c0c;
    --box-ink: #ffffff;
    --green: #3d5a3f;
    --green-light: #5a7a5c;
    --gold: #9c8433;
    --gold-light: #bfa552;
    --white-label: #f7f7f5;
    --white-shade: #e6e6e2;
    --brand-gold: #c9ae5d;
    --brand-gold-dark: #a88a36;
    --label-ink: #ffffff;
    --label-ink-dark: #4a4a4a;
  }
  * { box-sizing: border-box; margin: 0; padding: 0; }
  html, body { width: 1200px; height: 363px; overflow: hidden; background: var(--page); }
  .canvas { position: relative; width: 1200px; height: 363px; }

  .set { position: absolute; top: 0; width: 323px; height: 363px; }
  .set--green { left: 30px; }
  .set--gold { left: 428px; }
  .set--white { left: 826px; }

  .box-face {
    position: absolute; left: 0; top: 66px; width: 176px; height: 269px;
    background: var(--box-black);
    display: flex; flex-direction: column; align-items: center; justify-content: center;
    color: var(--box-ink); text-align: center;
    font-family: "Quicksand", sans-serif; font-weight: 500;
  }
  .mark-dot { width: 9px; height: 9px; border-radius: 50%; background: currentColor; margin-bottom: 6px; }
  .brand-name { font-size: 9px; line-height: 1.2; }
  .tagline { font-size: 5px; letter-spacing: 0.6px; margin-top: 3px; text-transform: uppercase; opacity: 0.85; }
  .product { font-size: 13px; line-height: 1.2; letter-spacing: 1px; margin-top: 8px; text-transform: uppercase; }

  .label {
    position: absolute; left: 186px; top: 217px; width: 137px; height: 118px;
    display: flex; flex-direction: column; align-items: center;
    padding-top: 22px; text-align: center;
    font-family: "Quicksand", sans-serif; font-weight: 500;
  }
  .label--green { background: linear-gradient(100deg, var(--green) 40%, var(--green-light)); color: var(--label-ink); }
  .label--gold { background: linear-gradient(100deg, var(--gold) 40%, var(--gold-light)); color: var(--label-ink); }
  .label--white { background: linear-gradient(100deg, var(--white-label) 45%, var(--white-shade)); color: var(--label-ink-dark); }
  .label .mark-dot { width: 7px; height: 7px; background: var(--brand-gold); margin-bottom: 5px; }
  .label .brand-name { font-size: 8px; color: var(--brand-gold); }
  .label .tagline { font-size: 4px; color: var(--brand-gold); }
  .label--gold .brand-name, .label--gold .tagline { color: #f3e3b0; }
  .label--white .brand-name, .label--white .tagline { color: var(--brand-gold-dark); }
  .label .product { font-size: 11px; margin-top: 6px; }
  .label-note { font-size: 4px; line-height: 1.5; width: 112px; margin-top: 10px; opacity: 0.85; }
</style>
</head>
<body>
<main class="canvas">
  <section class="set set--green">
    <div class="box-face">
      <span class="mark-dot"></span>
      <span class="brand-name">Serene Verses</span>
      <span class="tagline">Calm words for daily life</span>
      <span class="product">Quran Jar</span>
    </div>
    <div class="label label--green">
      <span class="mark-dot"></span>
      <span class="brand-name">Serene Verses</span>
      <span class="tagline">Calm words for daily life</span>
      <span class="product">Quran Jar</span>
      <p class="label-note">Thoughtful verses to read each day, drawn from the jar with calm intent and kept close to the heart.</p>
    </div>
  </section>

  <section class="set set--gold">
    <div class="box-face">
      <span class="mark-dot"></span>
      <span class="brand-name">Serene Verses</span>
      <span class="tagline">Calm words for daily life</span>
      <span class="product">Quran Jar</span>
    </div>
    <div class="label label--gold">
      <span class="mark-dot"></span>
      <span class="brand-name">Serene Verses</span>
      <span class="tagline">Calm words for daily life</span>
      <span class="product">Quran Jar</span>
      <p class="label-note">Thoughtful verses to read each day, drawn from the jar with calm intent and kept close to the heart.</p>
    </div>
  </section>

  <section class="set set--white">
    <div class="box-face">
      <span class="mark-dot"></span>
      <span class="brand-name">Serene Verses</span>
      <span class="tagline">Calm words for daily life</span>
      <span class="product">Quran Jar</span>
    </div>
    <div class="label label--white">
      <span class="mark-dot"></span>
      <span class="brand-name">Serene Verses</span>
      <span class="tagline">Calm words for daily life</span>
      <span class="product">Quran Jar</span>
      <p class="label-note">Thoughtful verses to read each day, drawn from the jar with calm intent and kept close to the heart.</p>
    </div>
  </section>
</main>
</body>
</html>
```